Brindle Sky Port needs a new upscale business card design for our high end aircraft hangar complex

Brindle Sky Port (BSP) is a large, upscale jet hangar complex in the US housing expensive aircraft. We need a new business card design, using our current logo. We will be attending a industry convention and need a card design that will stand out and be remembered by aircraft owners and private pilots.

Target Market(s)

Aircraft pilots or owners looking for a new upscale hangar

Industry/Entity Type

Airport

Contact Information for Business Card

I like to use very heavy card stock, 400#, double sided. Square, no rounded edges please.

Colors
3276b5
0255a3
85abd2

Requirements
Must have
• An expensive, classy design, vivid colors.
Nice to have
• Needs to look very expensive and classy, and have some "pop". Designer must be able to download or copy my current typeface or fonts.
• One card side might be black with the "Logo and Brindle Sky Port Double line image in blue (or try gold, or glossy black), and perhaps have a grayed out "K720 jet silhouette". The other card side would have our contact info, and perhaps the "BSP Logo only". I'd like my contact info 'stacked', not in a paragraph format.
Should not have
• Should not look "too busy". Having a double-sided card will help.

```html
<!DOCTYPE html>
<html lang="en">
<head>
<meta charset="utf-8">
<title>Brindle Sky Port – Business Card</title>
<link href="https://fonts.googleapis.com/css2?family=Open+Sans:wght@400;600;700&display=swap" rel="stylesheet">
<style>
  :root {
    --page-bg: #e9ebee;
    --card-top: #f3f5f7;
    --band-light: #1b8ac6;
    --band-dark: #0d5d9a;
    --brand-blue: #1d6fae;
    --text-light: #ffffff;
    --ghost-blue: #9db3c8;
  }
  * { margin: 0; padding: 0; box-sizing: border-box; }
  html, body {
    width: 1200px; height: 900px; overflow: hidden;
    background: var(--page-bg);
    font-family: "Open Sans", Arial, sans-serif;
  }
  .canvas { position: relative; width: 1200px; height: 900px; }

  .card {
    position: absolute;
    background: var(--card-top);
    box-shadow: 0 6px 20px rgba(0,0,0,0.12);
    overflow: hidden;
  }
  .card--front { left: 238px; top: 62px; width: 555px; height: 343px; }
  .card--back  { left: 459px; top: 519px; width: 560px; height: 342px; }

  .card__band {
    position: absolute; left: 0; right: 0; bottom: 0;
    background: linear-gradient(180deg, var(--band-light) 0%, var(--band-dark) 100%);
  }
  .card--front .card__band { height: 157px; }
  .card--back .card__band  { height: 156px; }

  .brand {
    position: absolute; left: 0; right: 0;
    text-align: center; color: var(--brand-blue); font-weight: 700;
    line-height: 1;
  }
  .brand__mark { font-size: 72px; letter-spacing: 4px; }
  .brand__name { font-size: 30px; margin-top: 14px; }
  .card--front .brand { top: 44px; }

  .card--back .brand {
    top: 40px; color: var(--ghost-blue); opacity: 0.75;
    transform: scaleX(-1);
  }

  .holder {
    position: absolute; left: 26px; top: 238px; color: var(--text-light);
  }
  .holder__name { font-size: 18px; font-weight: 700; line-height: 1.2; }
  .holder__role { font-size: 14px; font-weight: 400; margin-top: 2px; }

  .address {
    position: absolute; left: 190px; top: 229px;
    color: var(--text-light); font-size: 14px; line-height: 20px;
  }

  .contacts {
    position: absolute; left: 338px; top: 229px; list-style: none;
    color: var(--text-light); font-size: 14px; line-height: 20px;
  }
  .contacts li { display: flex; align-items: center; gap: 8px; }
  .contacts svg { width: 12px; height: 12px; fill: var(--text-light); flex: none; }

  .back-web {
    position: absolute; left: 0; right: 0; top: 293px;
    text-align: center; color: var(--text-light); font-size: 14px;
  }
</style>
</head>
<body>
<div class="canvas">

  <section class="card card--front">
    <div class="brand">
      <div class="brand__mark">BSP</div>
      <div class="brand__name">Brindle Sky Port</div>
    </div>
    <div class="card__band"></div>
    <div class="holder">
      <div class="holder__name">Harlan Pryce</div>
      <div class="holder__role">Managing Director</div>
    </div>
    <address class="address" style="font-style:normal">
      12345, Address<br>Goes Here Country<br>Name, 123456.
    </address>
    <ul class="contacts">
      <li>
        <svg viewBox="0 0 24 24" aria-hidden="true"><path d="M6.6 10.8a15.1 15.1 0 0 0 6.6 6.6l2.2-2.2c.3-.3.7-.4 1-.2 1.1.4 2.3.6 3.6.6.6 0 1 .4 1 1V20c0 .6-.4 1-1 1A17 17 0 0 1 3 4c0-.6.4-1 1-1h3.5c.6 0 1 .4 1 1 0 1.3.2 2.5.6 3.6.1.3 0 .7-.2 1z"/></svg>
        044-555 310 728
      </li>
      <li>
        <svg viewBox="0 0 24 24" aria-hidden="true"><path d="M2 5h20v14H2z M3.5 6.5 12 13l8.5-6.5" fill-rule="evenodd"/><path d="M2 5l10 7.5L22 5v1.8l-10 7.5L2 6.8z" fill="#0f6aa6"/></svg>
        info@brindleskyport.com
      </li>
      <li>
        <svg viewBox="0 0 24 24" aria-hidden="true"><circle cx="12" cy="12" r="10"/><path d="M7 8c2 0 3 1 3 3s2 2 2 4-1 3-2 4M15 4c0 2 1 3 3 3s2 2 3 2" stroke="#0f6aa6" stroke-width="2" fill="none"/></svg>
        www.brindleskyport.com
      </li>
    </ul>
  </section>

  <section class="card card--back">
    <div class="brand" aria-hidden="true">
      <div class="brand__mark">BSP</div>
      <div class="brand__name">Brindle Sky Port</div>
    </div>
    <div class="card__band"></div>
    <div class="back-web">www.brindleskyport.com</div>
  </section>

</div>
</body>
</html>
```